Website to design and sell sundials: www.gnomonvale.com

We have a website that creates a free paper sundial, we want to migrate from this not profit free website to a website where we will continue offering the free paper sundial model but We will also offer a manufactured sundial and sell it.
In order to understand the project, please visit:
http://www.gnomonvale.com/vertical/sundial.html and
http://www.torvel.net/landing/

The website user journey should be redesigned, including the phases that are,
select language
Show product give info
Creation/edit sundial (could be one or more phases)
View created sundial
Buy sundial.

May some of them could be combined or splitted, what It have more sense.

Requirements
Must have
• A description page user journey offering freemium paper sundial and physical sundial to sell.
• A sundial creation page for "free" paper sundial
• A result page for paper sundial
• A sell page for physical

```html
<!DOCTYPE html>
<html lang="en">
<head>
<meta charset="utf-8">
<title>GnomonVale — Sundials</title>
<link href="https://fonts.googleapis.com/css2?family=Roboto:wght@400;500;700&display=swap" rel="stylesheet">
<style>
:root{
  --red:#c4120d;
  --red-bright:#e0261f;
  --salmon:#e8584c;
  --orange:#f3a42c;
  --gold:#f5b430;
  --ink:#222;
  --text:#444;
  --white:#fff;
  --brown:#361a0b;
  --bar:#f4a93a;
  --black:#0b0b0b;
}
*{margin:0;padding:0;box-sizing:border-box}
html,body{width:1200px;height:2406px;overflow:hidden}
body{position:relative;background:var(--white);font-family:'Roboto',Arial,sans-serif;color:var(--text)}
.abs{position:absolute}

/* header */
.site-header{position:absolute;left:0;top:0;width:1200px;height:104px;background:var(--white)}
.brand{position:absolute;display:flex;align-items:center;gap:12px;font-weight:500;color:var(--red);font-family:'Roboto',Arial,sans-serif}
.brand .dot{width:22px;height:22px;border-radius:50%;background:var(--red)}
.site-header .brand{left:80px;top:30px;font-size:30px}
.lang{position:absolute;left:762px;top:9px;width:120px;height:27px;border:1px solid #ccc;font-size:12px;color:#555;display:flex;align-items:center;padding-left:10px;gap:6px}
.lang .flag{width:14px;height:14px;border-radius:50%;background:#2a4da0;border:2px solid #d22}
.call{position:absolute;left:921px;top:13px;font-size:12px;color:#444}
.call b{font-size:20px;color:var(--red);font-weight:700;margin-left:4px}
.main-nav{position:absolute;top:69px;left:595px;display:flex;gap:0;font-size:12px;color:var(--red)}
.main-nav a{color:var(--red);text-decoration:none;text-transform:uppercase;position:absolute;white-space:nowrap}

/* hero */
.hero{position:absolute;left:0;top:104px;width:1200px;height:534px;background:radial-gradient(ellipse at 70% 35%,#5b6064 0%,#33383c 45%,#15191c 100%)}
.hero h1{position:absolute;left:80px;top:222px;font-size:45px;font-weight:700;color:var(--gold);letter-spacing:.5px}
.pill{position:absolute;left:83px;top:284px;width:177px;height:46px;border-radius:23px;background:var(--red);color:var(--white);font-size:15px;font-weight:700;display:flex;align-items:center;justify-content:center}
.dots{position:absolute;left:538px;top:499px;display:flex;gap:19px}
.dots span{width:11px;height:11px;border-radius:50%;border:2px solid var(--white)}
.dots .on{background:var(--orange);border-color:var(--orange)}

/* custom */
.photo{position:absolute;border:2px solid #111}
.custom-photo{left:80px;top:695px;width:551px;height:369px;background:radial-gradient(ellipse at 55% 50%,#d9dde2 0%,#aab1b8 30%,#4f6a2a 55%,#2f4418 100%)}
.section-title{position:absolute;font-weight:700;text-transform:uppercase}
.custom h2{left:675px;top:697px;font-size:27px;color:var(--red)}
.custom .lead{position:absolute;left:676px;top:740px;width:450px;font-size:13px;line-height:17px;color:#333}
.custom .spec{position:absolute;left:676px;top:789px;font-size:13px;color:var(--orange);text-transform:uppercase}
.spec-list{position:absolute;left:676px;top:822px;list-style:none}
.spec-list li{height:31px;font-size:13px;color:#444;display:flex;align-items:center;gap:14px}
.spec-list svg{width:14px;height:14px}
.btn-order{position:absolute;left:675px;top:1017px;width:151px;height:46px;background:var(--salmon);color:var(--white);font-size:13px;font-weight:500;display:flex;align-items:center;justify-content:center;gap:10px;border-radius:2px}

/* options */
.options{position:absolute;left:0;top:1123px;width:1200px;height:507px;background:linear-gradient(135deg,#b3100c 0%,#c8160f 50%,#ad0e0a 100%)}
.opt-photo-1{left:85px;top:38px;width:305px;height:194px;background:linear-gradient(90deg,#7a8a99 0%,#d9dbe0 40%,#a44d36 70%,#8c3c28 100%)}
.opt-photo-2{left:85px;top:268px;width:305px;height:194px;background:linear-gradient(90deg,#1e2420 0%,#c3b39b 40%,#8e969b 80%,#5b6367 100%)}
.opt-arrow{position:absolute;left:390px;top:113px}
.options h2{left:480px;top:52px;font-size:26px;color:var(--white)}
.options .intro{position:absolute;left:480px;top:113px;width:632px;font-size:13px;line-height:24px;color:var(--white)}
.field-label{position:absolute;font-size:13px;font-weight:700;color:var(--white);text-transform:uppercase}
.field{position:absolute;width:307px;height:36px;background:var(--white);border-radius:2px;font-size:11px;color:#333;display:flex;align-items:center;padding:0 14px;justify-content:space-between}
.btn-create{position:absolute;left:812px;top:404px;width:306px;height:48px;background:var(--red-bright);color:var(--white);font-size:16px;font-weight:500;display:flex;align-items:center;justify-content:center;border-radius:2px;box-shadow:0 2px 0 #9a0c08}

/* buy */
.buy h2{left:0;width:1200px;text-align:center;top:1667px;font-size:26px;color:#2a1608}
.card{position:absolute;top:1729px;width:246px}
.card .pic{height:181px;border:1px solid #ccc}
.card p{margin-top:17px;padding-left:4px;font-size:12px;line-height:21px;color:#444}
.card .bar{position:absolute;top:254px;left:0;width:246px;height:36px;background:var(--black);display:flex;align-items:center;padding-left:15px;font-size:12px;color:var(--white)}
.card .bar i{color:var(--red-bright);font-style:normal;margin-left:2px}
.card .cart{position:absolute;right:0;top:0;width:51px;height:36px;background:var(--red-bright);display:flex;align-items:center;justify-content:center}

/* footer */
.site-footer{position:absolute;left:0;top:2072px;width:1200px;height:283px;background:var(--brown);color:var(--white)}
.site-footer .brand{left:80px;top:62px;font-size:24px}
.site-footer .brand .dot{width:18px;height:18px}
.about{position:absolute;left:80px;top:118px;width:335px;font-size:13px;line-height:23px;text-align:justify}
.social{position:absolute;left:82px;top:205px;display:flex;gap:22px}
.social span{width:14px;height:14px;border-radius:50%;background:var(--orange)}
.foot-title{position:absolute;top:58px;font-size:15px;font-weight:700;color:var(--orange);text-transform:uppercase}
.contact-line{position:absolute;left:502px;display:flex;gap:16px;font-size:13px;line-height:18px}
.contact-line svg{width:16px;height:18px;flex:none}
.foot-links{position:absolute;top:112px;list-style:none;font-size:13px}
.foot-links li{height:28.5px}
.copyright{position:absolute;left:0;top:2355px;width:1200px;height:51px;background:var(--bar);font-size:13px;color:#3a2410;display:flex;align-items:center;justify-content:center}
</style>
</head>
<body>

<header class="site-header">
  <div class="brand"><span class="dot"></span>GnomonVale</div>
  <div class="lang">LANGUAGE <span class="flag"></span> &#8964;</div>
  <div class="call">CALL US : <b>555-301-7744</b></div>
  <nav class="main-nav">
    <a style="left:0">Home</a>
    <a style="left:103px">About</a>
    <a style="left:171px">Products</a>
    <a style="left:282px">News</a>
    <a style="left:365px">Gallery</a>
    <a style="left:465px">Contact</a>
  </nav>
</header>

<section class="hero" role="img" aria-label="Close-up photograph of a metal sundial gnomon casting a shadow on its dial plate">
  <h1>LOREM IPSUM DOLOR SIT AMET</h1>
  <div class="pill">ORDER NOW</div>
  <div class="dots"><span></span><span></span><span class="on"></span><span></span><span></span></div>
</section>

<section class="custom">
  <div class="photo custom-photo" role="img" aria-label="Customized flat sundial plate with hour lines lying on grass"></div>
  <h2 class="section-title">Build your customized sundial</h2>
  <p class="lead">We can manufacture your Sundial, design to your specific location. Becoming a unique piece considering your location, and wall declination.</p>
  <div class="spec">Specifications:</div>
  <ul class="spec-list">
    <li><svg viewBox="0 0 14 14"><circle cx="7" cy="7" r="7" fill="#f3a42c"/><path d="M5.5 4l3 3-3 3" stroke="#fff" stroke-width="1.6" fill="none"/></svg>Size 245mm x 345 mm</li>
    <li><svg viewBox="0 0 14 14"><circle cx="7" cy="7" r="7" fill="#f3a42c"/><path d="M5.5 4l3 3-3 3" stroke="#fff" stroke-width="1.6" fill="none"/></svg>Methacrylate board 3mm thick with rounded corners.</li>
    <li><svg viewBox="0 0 14 14"><circle cx="7" cy="7" r="7" fill="#f3a42c"/><path d="M5.5 4l3 3-3 3" stroke="#fff" stroke-width="1.6" fill="none"/></svg>Steeel like cover</li>
    <li><svg viewBox="0 0 14 14"><circle cx="7" cy="7" r="7" fill="#f3a42c"/><path d="M5.5 4l3 3-3 3" stroke="#fff" stroke-width="1.6" fill="none"/></svg>Customized laser engravement with line hours</li>
    <li><svg viewBox="0 0 14 14"><circle cx="7" cy="7" r="7" fill="#f3a42c"/><path d="M5.5 4l3 3-3 3" stroke="#fff" stroke-width="1.6" fill="none"/></svg>Customized Gnomon 3mm black with fitting on board tabs.</li>
    <li><svg viewBox="0 0 14 14"><circle cx="7" cy="7" r="7" fill="#f3a42c"/><path d="M5.5 4l3 3-3 3" stroke="#fff" stroke-width="1.6" fill="none"/></svg>Shipping to EU</li>
  </ul>
  <div class="btn-order">
    <svg width="26" height="22" viewBox="0 0 26 22"><path d="M1 2h4l3 12h13l3-9H7" fill="none" stroke="#fff" stroke-width="2"/><circle cx="10" cy="19" r="2" fill="#fff"/><circle cx="19" cy="19" r="2" fill="#fff"/></svg>
    ORDER NOW
  </div>
</section>

<section class="options">
  <div class="photo opt-photo-1" role="img" aria-label="Vertical sundial mounted on a brick wall"></div>
  <svg class="opt-arrow" width="30" height="40" viewBox="0 0 30 40"><path d="M0 0L30 20L0 40Z" fill="#111"/></svg>
  <div class="photo opt-photo-2" role="img" aria-label="Vertical sundial on a wall overlooking a terrace"></div>
  <h2 class="section-title">Sundial options</h2>
  <p class="intro">Lorem ipsum dolor sit amet, consectetur adipiscing elit. Ut auctor lorem vitae dui fringilla, sed vulp utate massa rhoncus. Cras tincidunt semper elit vitae porta. Quisque in turpis id leo viverra cursus vel in ligula.</p>
  <div class="field-label" style="left:486px;top:213px">Banner</div>
  <div class="field" style="left:486px;top:240px"></div>
  <div class="field-label" style="left:811px;top:213px">Timezone</div>
  <div class="field" style="left:810px;top:240px">(GMT+999) LOCAL TIME (SOLAR TIME) <span>&#8964;</span></div>
  <div class="field-label" style="left:486px;top:311px">Times</div>
  <div class="field" style="left:486px;top:338px"></div>
  <div class="field-label" style="left:811px;top:311px">Daylight saving time</div>
  <div class="field" style="left:810px;top:338px"></div>
  <div class="btn-create">CREATE SUNDIAL</div>
</section>

<section class="buy">
  <h2 class="section-title">Buy sundial</h2>
  <div class="card" style="left:80px">
    <div class="pic" role="img" aria-label="Brass engraved garden sundial" style="background:radial-gradient(circle at 45% 50%,#e3c98a,#b58f4a 60%,#7d6a58)"></div>
    <p>Lorem ipsum dolor sit amet, consectetur adipiscing elit</p>
    <div class="bar">View Features <i>&raquo;</i><span class="cart"><svg width="18" height="16" viewBox="0 0 26 22"><path d="M1 2h4l3 12h13l3-9H7" fill="none" stroke="#fff" stroke-width="2.5"/><circle cx="10" cy="19" r="2.5" fill="#fff"/><circle cx="19" cy="19" r="2.5" fill="#fff"/></svg></span></div>
  </div>
  <div class="card" style="left:343px">
    <div class="pic" role="img" aria-label="Stone paved ground sundial with numerals" style="background:radial-gradient(circle at 50% 45%,#c9c4bb,#9a948c 55%,#6e6a66)"></div>
    <p>Lorem ipsum dolor sit amet, consectetur adipiscing elit</p>
    <div class="bar">View Features <i>&raquo;</i><span class="cart"><svg width="18" height="16" viewBox="0 0 26 22"><path d="M1 2h4l3 12h13l3-9H7" fill="none" stroke="#fff" stroke-width="2.5"/><circle cx="10" cy="19" r="2.5" fill="#fff"/><circle cx="19" cy="19" r="2.5" fill="#fff"/></svg></span></div>
  </div>
  <div class="card" style="left:608px">
    <div class="pic" role="img" aria-label="Weathered metal sundial with dark gnomon" style="background:radial-gradient(circle at 50% 50%,#b7bdbf,#7f8a8c 55%,#2e3a2c)"></div>
    <p>Lorem ipsum dolor sit amet, consectetur adipiscing elit</p>
    <div class="bar">View Features <i>&raquo;</i><span class="cart"><svg width="18" height="16" viewBox="0 0 26 22"><path d="M1 2h4l3 12h13l3-9H7" fill="none" stroke="#fff" stroke-width="2.5"/><circle cx="10" cy="19" r="2.5" fill="#fff"/><circle cx="19" cy="19" r="2.5" fill="#fff"/></svg></span></div>
  </div>
  <div class="card" style="left:873px">
    <div class="pic" role="img" aria-label="Pedestal sundial in a garden" style="background:radial-gradient(circle at 50% 45%,#8c8d96,#4f5360 45%,#4c6a2e)"></div>
    <p>Lorem ipsum dolor sit amet, consectetur adipiscing elit</p>
    <div class="bar">View Features <i>&raquo;</i><span class="cart"><svg width="18" height="16" viewBox="0 0 26 22"><path d="M1 2h4l3 12h13l3-9H7" fill="none" stroke="#fff" stroke-width="2.5"/><circle cx="10" cy="19" r="2.5" fill="#fff"/><circle cx="19" cy="19" r="2.5" fill="#fff"/></svg></span></div>
  </div>
</section>

<footer class="site-footer">
  <div class="brand"><span class="dot"></span>GnomonVale</div>
  <p class="about">Lorem ipsum dolor sit amet, consectetur adipiscing elit. Etiam bibendum purus quis ipsum auctor malesuada. Mauris sit amet lectus libero. Sed id felis mattis laoreet.</p>
  <div class="social"><span></span><span></span><span></span><span></span><span></span></div>

  <div class="foot-title" style="left:502px;top:60px">Contact us</div>
  <div class="contact-line" style="top:117px"><svg viewBox="0 0 16 18"><path d="M8 1a5.5 5.5 0 0 0-5.5 5.5C2.5 11 8 17 8 17s5.5-6 5.5-10.5A5.5 5.5 0 0 0 8 1z" fill="#f3a42c"/><circle cx="8" cy="6.5" r="2" fill="#361a0b"/></svg><span>41 Quarry Row, Bellmont Lane<br>Fairhaven 402719</span></div>
  <div class="contact-line" style="top:168px"><svg viewBox="0 0 16 18"><path d="M3 2l3 0 1.5 4-2 1.5a9 9 0 0 0 4 4L11 9.5l4 1.5v3c0 1-1 2-2 2C7 16 1 10 1 4c0-1 1-2 2-2z" fill="#f3a42c"/></svg><span>+10 (800) 555 0147</span></div>
  <div class="contact-line" style="top:203px"><svg viewBox="0 0 16 18"><rect x="1" y="4" width="14" height="10" fill="#f3a42c"/><path d="M1 4l7 6 7-6" stroke="#361a0b" stroke-width="1.4" fill="none"/></svg><span>support@gnomonvale.com</span></div>

  <div class="foot-title" style="left:819px">Company</div>
  <ul class="foot-links" style="left:820px"><li>Home</li><li>Why Us?</li><li>Products</li><li>Testimonials</li><li>Contact</li></ul>

  <div class="foot-title" style="left:1016px;top:60px">Quick links</div>
  <ul class="foot-links" style="left:1018px"><li>Faq</li><li>News</li><li>About us</li><li>Privacy Policy</li><li>Terms of Use</li></ul>
</footer>

<div class="copyright">Sundial &copy; 2016 All Rights Reserved.</div>

</body>
</html>
```